Floor Inspections and Consulting

We provide inspections and consulting services on various floor coverings, e.g. carpet, hardwood, etc. We also do expert witness work for attorneys due to floor covering failures. We current have a logo, just need it incorporated into a new design. I have examples of cards I have found on the internet that capture my attention and make a statement. I have included our original business card, which in my opinion is terrible, but it does have our logo on it.

```html
<!DOCTYPE html>
<html lang="en">
<head>
<meta charset="utf-8">
<title>Keystone Floor Inspections – Business Cards</title>
<link rel="stylesheet" href="https://fonts.googleapis.com/css2?family=Archivo+Black&family=Arimo:wght@400;700&display=swap">
<style>
  :root {
    --page-bg: #d9d9d7;
    --wood-light: #b0683a;
    --wood-mid: #9a5630;
    --wood-dark: #7e4324;
    --ink: #120a05;
    --shadow: rgba(0, 0, 0, 0.35);
  }
  * { box-sizing: border-box; margin: 0; padding: 0; }
  html, body {
    width: 1200px;
    height: 1015px;
    overflow: hidden;
    background: var(--page-bg);
  }
  .canvas {
    position: relative;
    width: 1200px;
    height: 1015px;
    display: flex;
    flex-direction: column;
    align-items: center;
    justify-content: center;
    gap: 56px;
  }
  .card {
    position: relative;
    width: 680px;
    height: 388px;
    border-radius: 4px;
    overflow: hidden;
    box-shadow: 0 14px 30px var(--shadow);
    color: var(--ink);
  }
  .card-surface {
    position: absolute;
    inset: 0;
    background: linear-gradient(100deg, var(--wood-light) 0%, var(--wood-mid) 45%, var(--wood-dark) 100%);
  }
  .card-content {
    position: relative;
    height: 100%;
  }

  /* Front */
  .front .brand {
    position: absolute;
    left: 92px;
    top: 108px;
    display: flex;
    align-items: center;
    gap: 22px;
  }
  .brand-square {
    width: 96px;
    height: 96px;
    background: var(--ink);
    flex: none;
  }
  .brand-name {
    font-family: "Archivo Black", sans-serif;
    font-size: 34px;
    line-height: 1.02;
    letter-spacing: 1px;
    text-transform: uppercase;
  }
  .front .service-line {
    position: absolute;
    left: 92px;
    top: 226px;
    width: 500px;
    padding: 6px 0;
    border-top: 3px solid var(--ink);
    font-family: "Archivo Black", sans-serif;
    font-size: 15px;
    letter-spacing: 3px;
    text-transform: uppercase;
  }
  .front .tagline {
    position: absolute;
    left: 92px;
    top: 300px;
    font-family: "Arimo", sans-serif;
    font-weight: 700;
    font-size: 20px;
    letter-spacing: 0.3px;
  }

  /* Back */
  .back .brand {
    position: absolute;
    left: 70px;
    top: 70px;
    display: flex;
    align-items: center;
    gap: 20px;
  }
  .back .brand-square { width: 110px; height: 110px; }
  .back .brand-name { font-size: 30px; }
  .contact {
    position: absolute;
    left: 280px;
    top: 208px;
  }
  .person-name {
    font-family: "Archivo Black", sans-serif;
    font-size: 24px;
    letter-spacing: 1px;
    text-transform: uppercase;
    margin-bottom: 16px;
  }
  .contact-list { list-style: none; }
  .contact-item {
    display: flex;
    align-items: center;
    gap: 10px;
    font-family: "Arimo", sans-serif;
    font-size: 20px;
    line-height: 1.45;
  }
  .contact-icon { width: 20px; height: 20px; flex: none; }
</style>
</head>
<body>
<main class="canvas">

  <section class="card front">
    <div class="card-surface" role="img" aria-label="Warm teak wood grain card surface"></div>
    <div class="card-content">
      <div class="brand">
        <span class="brand-square"></span>
        <p class="brand-name">Keystone<br>Floor<br>Inspections</p>
      </div>
      <p class="service-line">Analysis &amp; Consulting</p>
      <p class="tagline">Certified Floor Covering Inspection &amp; Consulting</p>
    </div>
  </section>

  <section class="card back">
    <div class="card-surface" role="img" aria-label="Warm teak wood grain card surface"></div>
    <div class="card-content">
      <div class="brand">
        <span class="brand-square"></span>
        <p class="brand-name">Keystone<br>Floor<br>Inspections</p>
      </div>
      <div class="contact">
        <p class="person-name">Daniel Harlow</p>
        <ul class="contact-list">
          <li class="contact-item">
            <svg class="contact-icon" viewBox="0 0 20 20" aria-hidden="true">
              <rect x="1" y="1" width="18" height="18" rx="3" fill="none" stroke="#120a05" stroke-width="2"/>
              <path d="M6 5 L8 5 L9 8 L7.5 9 Q9 12 11 12.5 L12 11 L15 12 L15 14 Q11 15 8 12 Q5 9 6 5 Z" fill="#120a05"/>
            </svg>
            303-555-0147
          </li>
          <li class="contact-item">
            <svg class="contact-icon" viewBox="0 0 20 20" aria-hidden="true">
              <rect x="1" y="4" width="18" height="12" fill="#120a05"/>
              <path d="M1 4 L10 11 L19 4" fill="none" stroke="#b0683a" stroke-width="1.5"/>
            </svg>
            daniel@keystonefloorpro.com
          </li>
          <li class="contact-item">
            <svg class="contact-icon" viewBox="0 0 20 20" aria-hidden="true">
              <circle cx="10" cy="10" r="9" fill="#120a05"/>
              <ellipse cx="10" cy="10" rx="4" ry="9" fill="none" stroke="#b0683a" stroke-width="1.2"/>
              <line x1="1" y1="10" x2="19" y2="10" stroke="#b0683a" stroke-width="1.2"/>
              <line x1="10" y1="1" x2="10" y2="19" stroke="#b0683a" stroke-width="1.2"/>
            </svg>
            www.keystonefloorpro.com
          </li>
        </ul>
      </div>
    </div>
  </section>

</main>
</body>
</html>
```